New Webpage for High Class Expert Witness Services Company

We are looking for a minimalist design for a webpage that just has our logo and an entry form offer to connect with one of our Liaisons.
The entry form should just ask for Name, Email, Contact Info and Description of Project.

Company Name is: The Marlowe Crest Advisory Services

Number of Pages Required

1 page

```html
<!DOCTYPE html>
<html lang="en">
<head>
<meta charset="utf-8">
<title>The Marlowe Crest Advisory Services – Contact</title>
<link rel="stylesheet" href="https://fonts.googleapis.com/css2?family=Cormorant+Garamond:wght@600;700&family=Poppins:wght@400;500;600&display=swap">
<style>
  :root {
    --ink: #1f2328;
    --muted: #4a4f55;
    --orange: #fb8122;
    --red: #c0262d;
    --white: #ffffff;
    --rule: #c9ccd1;
  }
  * { box-sizing: border-box; margin: 0; padding: 0; }
  html, body { width: 1091px; height: 1200px; overflow: hidden; background: var(--white); }
  body { position: relative; font-family: "Poppins", sans-serif; color: var(--ink); }

  .site-header { position: absolute; left: 0; top: 0; width: 1091px; height: 73px; border-bottom: 2px dotted var(--rule); }
  .brand { position: absolute; left: 109px; top: 22px; font-family: "Cormorant Garamond", serif; font-weight: 700; font-size: 19px; line-height: 1; letter-spacing: .3px; }
  .brand small { display: block; font-family: "Poppins", sans-serif; font-weight: 500; font-size: 7px; letter-spacing: 2px; margin-top: 4px; color: var(--muted); }
  .call-button { position: absolute; left: 812px; top: 18px; width: 170px; height: 37px; background: var(--orange); color: var(--white); display: flex; align-items: center; justify-content: center; gap: 8px; font-size: 14px; font-weight: 500; letter-spacing: .3px; }

  .hero { position: absolute; left: 0; top: 74px; width: 1091px; height: 726px; border-bottom: 2px dashed var(--red);
    background: linear-gradient(180deg, #dbe8f4 0%, #c8dbea 40%, #5f97b2 62%, #2f7390 100%); }
  .hero-bridge { position: absolute; left: 0; top: 0; width: 300px; height: 726px;
    background: linear-gradient(90deg, rgba(196,48,32,.85) 0%, rgba(196,48,32,.55) 40%, rgba(196,48,32,0) 100%); }
  .hero-title { position: absolute; left: 0; width: 100%; top: 48px; text-align: center; font-family: "Cormorant Garamond", serif; font-weight: 700; font-size: 37px; letter-spacing: 1px; }
  .hero-sub { position: absolute; left: 0; width: 100%; top: 96px; text-align: center; font-size: 16px; letter-spacing: .8px; color: var(--muted); }

  .contact-card { position: absolute; left: 218px; top: 149px; width: 655px; height: 508px; border: 1px solid rgba(255,255,255,.8); border-radius: 5px; background: rgba(235,240,246,.55); box-shadow: 0 10px 30px rgba(0,0,0,.18); }
  .card-title { position: absolute; top: 40px; width: 100%; text-align: center; font-size: 19px; letter-spacing: 1px; }
  .field { position: absolute; left: 73px; width: 509px; height: 44px; border-radius: 22px; background: var(--white); box-shadow: 0 2px 6px rgba(0,0,0,.12); padding: 13px 0 0 32px; font-size: 11.5px; font-weight: 500; letter-spacing: .5px; }
  .field .req { color: var(--red); }
  .field-name { top: 83px; } .field-email { top: 138px; } .field-phone { top: 192px; }
  .field-message { top: 247px; height: 145px; border-radius: 22px; padding-top: 16px; }
  .submit { position: absolute; left: 229px; top: 418px; width: 197px; height: 43px; background: var(--orange); color: var(--white); font-weight: 600; font-size: 14.5px; letter-spacing: .8px; display: flex; align-items: center; justify-content: center; }

  .footer-brand { position: absolute; left: 109px; top: 876px; font-family: "Cormorant Garamond", serif; font-weight: 700; font-size: 27px; line-height: 1; }
  .copyright { position: absolute; left: 109px; top: 939px; font-size: 12.3px; line-height: 20px; letter-spacing: .2px; }
  .social { position: absolute; left: 109px; top: 1002px; display: flex; gap: 15px; }
  .social span { width: 13px; height: 13px; border-radius: 50%; background: var(--ink); }

  .col-title { position: absolute; top: 877px; font-size: 14px; font-weight: 600; letter-spacing: .3px; }
  .sitemap-title { left: 438px; } .contact-title { left: 628px; }
  .sitemap { position: absolute; left: 438px; top: 919px; list-style: none; font-size: 12px; letter-spacing: .4px; }
  .sitemap li { height: 29px; }
  .sitemap .caret { font-size: 8px; margin-left: 3px; }

  .dot-icon { position: absolute; width: 29px; height: 29px; border-radius: 50%; background: var(--orange); display: flex; align-items: center; justify-content: center; }
  .info { position: absolute; font-size: 10.5px; line-height: 15px; letter-spacing: .2px; }
</style>
</head>
<body>
  <header class="site-header">
    <div class="brand">The Marlowe Crest<small>ADVISORY SERVICES</small></div>
    <div class="call-button">
      <svg width="13" height="13" viewBox="0 0 24 24" fill="#fff"><path d="M6.6 10.8a15.1 15.1 0 0 0 6.6 6.6l2.2-2.2c.3-.3.7-.4 1-.2 1.1.4 2.3.6 3.6.6.6 0 1 .4 1 1V20c0 .6-.4 1-1 1A17 17 0 0 1 3 4c0-.6.4-1 1-1h3.5c.6 0 1 .4 1 1 0 1.3.2 2.5.6 3.6.1.3 0 .7-.2 1z"/></svg>
      (415) 555-0182
    </div>
  </header>

  <section class="hero">
    <div class="hero-bridge" role="img" aria-label="Photograph of a red suspension bridge over a bay with coastline"></div>
    <h1 class="hero-title">ADVISORY SERVICES</h1>
    <p class="hero-sub">Contact our Advisory Liaisons</p>

    <form class="contact-card">
      <h2 class="card-title">Connect With Us</h2>
      <div class="field field-name">Name<span class="req">*</span></div>
      <div class="field field-email">Email<span class="req">*</span></div>
      <div class="field field-phone">Contact number<span class="req">*</span></div>
      <div class="field field-message">Description of Project...</div>
      <div class="submit">SUBMIT</div>
    </form>
  </section>

  <footer>
    <div class="footer-brand">Marlowe Crest</div>
    <p class="copyright">Copyright © 2026 The Marlowe Crest Group<br>All Rights Reserved.</p>
    <div class="social"><span></span><span></span><span></span><span></span><span></span></div>

    <h3 class="col-title sitemap-title">SITE MAP</h3>
    <ul class="sitemap">
      <li>Stakeholders</li>
      <li>Physicians</li>
      <li>Services<span class="caret">▼</span></li>
      <li>Education<span class="caret">▼</span></li>
      <li>News</li>
      <li>Contact Us</li>
    </ul>

    <h3 class="col-title contact-title">CONTACT INFO</h3>
    <div class="dot-icon" style="left:628px;top:920px">
      <svg width="11" height="13" viewBox="0 0 24 28" fill="#fff"><path d="M12 0a10 10 0 0 0-10 10c0 7.5 10 18 10 18s10-10.5 10-18A10 10 0 0 0 12 0zm0 14a4 4 0 1 1 0-8 4 4 0 0 1 0 8z"/></svg>
    </div>
    <p class="info" style="left:663px;top:921px">48 Harbor Lane / 3rd Floor /<br>San Francisco, CA 94105</p>
    <p class="info" style="left:663px;top:967px">310 Bayview Ct / Ste 140 /<br>Santa Ana, CA 92704</p>

    <div class="dot-icon" style="left:870px;top:920px">
      <svg width="12" height="12" viewBox="0 0 24 24" fill="#fff"><path d="M6.6 10.8a15.1 15.1 0 0 0 6.6 6.6l2.2-2.2c.3-.3.7-.4 1-.2 1.1.4 2.3.6 3.6.6.6 0 1 .4 1 1V20c0 .6-.4 1-1 1A17 17 0 0 1 3 4c0-.6.4-1 1-1h3.5c.6 0 1 .4 1 1 0 1.3.2 2.5.6 3.6.1.3 0 .7-.2 1z"/></svg>
    </div>
    <p class="info" style="left:905px;top:926px">(800) 555-0147</p>
    <div class="dot-icon" style="left:870px;top:961px">
      <svg width="12" height="12" viewBox="0 0 24 24" fill="#fff"><rect x="3" y="8" width="18" height="12" rx="2"/><rect x="2" y="4" width="20" height="4" rx="2"/></svg>
    </div>
    <p class="info" style="left:905px;top:967px">(415) 555-0182</p>
  </footer>
</body>
</html>
```